Tech business card design

We need an amazing business card design for our new business 'Pexla' a marketing tech startup based in Sydney, Australia. We provide an online marketplace for businesses to search and buy advertising media, connect with service providers and learn more about marketing. We wish to communicate 'cool tech', reliability and professionalism and design based around our logo.

Target Market(s)

Business Owners

Contact Information for Business Card

Name
Position
Email Address
Website
Phone Number

Font styles to use
Other font styles liked:
• Avenir & Avenir Next

Colors

Designer to choose colors to be used in the design.

```html
<!DOCTYPE html>
<html lang="en">
<head>
<meta charset="utf-8">
<title>Pexla Business Card</title>
<link href="https://fonts.googleapis.com/css2?family=Rubik:wght@400;500;700&display=swap" rel="stylesheet">
<style>
  :root {
    --navy: #11123b;
    --navy-soft: #1d1f55;
    --paper: #ffffff;
    --ink-grey: #6b6b74;
    --rule: #2a2c5e;
    --backdrop: #d9d9dc;
  }
  * { margin: 0; padding: 0; box-sizing: border-box; }
  html, body {
    width: 1200px; height: 930px; overflow: hidden;
    background: var(--backdrop);
    font-family: "Rubik", Arial, sans-serif;
  }
  .sheet {
    width: 1200px; height: 930px;
    display: flex; flex-direction: column;
    align-items: center; justify-content: center; gap: 50px;
  }
  .card {
    position: relative;
    width: 700px; height: 400px;
    border-radius: 26px;
    overflow: hidden;
  }
  .card--back {
    background: var(--navy);
    display: flex; align-items: center; justify-content: center;
  }
  .card--back .wordmark {
    color: var(--paper);
    font-size: 120px; font-weight: 700; letter-spacing: -3px;
  }
  .card--front { background: var(--paper); }
  .card__swoosh { position: absolute; inset: 0; }
  .card--front .wordmark {
    position: absolute; left: 44px; top: 190px;
    color: var(--navy);
    font-size: 96px; font-weight: 700; letter-spacing: -2px; line-height: 1;
  }
  .identity {
    position: absolute; right: 40px; top: 96px;
    text-align: right;
    width: 260px;
    border-bottom: 1.5px solid var(--rule);
    padding-bottom: 8px;
  }
  .identity__name { color: var(--navy); font-size: 25px; font-weight: 500; }
  .identity__role { color: var(--ink-grey); font-size: 14px; margin-top: 2px; }
  .address {
    position: absolute; right: 40px; top: 200px;
    text-align: right; color: var(--ink-grey);
    font-size: 16px; line-height: 1.45;
  }
  .divider {
    position: absolute; left: 44px; right: 40px; top: 318px;
    border-top: 1.5px solid var(--rule);
  }
  .contacts {
    position: absolute; left: 44px; top: 326px;
    list-style: none; color: var(--ink-grey); font-size: 15px; line-height: 21px;
  }
  .contacts li { display: flex; align-items: center; gap: 10px; }
  .contacts svg { width: 12px; height: 12px; fill: var(--navy); flex: none; }
</style>
</head>
<body>
<main class="sheet">
  <section class="card card--back">
    <span class="wordmark">pexla</span>
  </section>

  <section class="card card--front">
    <svg class="card__swoosh" viewBox="0 0 700 400" aria-hidden="true">
      <path d="M0 0 H700 V20 C560 40 250 80 0 260 Z" fill="var(--navy)"/>
      <path d="M0 210 C230 70 520 30 700 12" fill="none" stroke="var(--paper)" stroke-width="3"/>
      <path d="M0 228 C240 92 520 44 700 22" fill="none" stroke="var(--paper)" stroke-width="2"/>
    </svg>

    <span class="wordmark">pexla</span>

    <div class="identity">
      <p class="identity__name">Daniel Harper</p>
      <p class="identity__role">Director</p>
    </div>

    <address class="address">
      812 Orchard Lane<br>Riverton, NC 28301
    </address>

    <div class="divider"></div>

    <ul class="contacts">
      <li><svg viewBox="0 0 12 12"><path d="M2.5 1 L4.5 1 L5.2 3.6 L4 4.6 C4.7 6 6 7.3 7.4 8 L8.4 6.8 L11 7.5 L11 9.5 C11 10.3 10.3 11 9.5 11 C5 11 1 7 1 2.5 C1 1.7 1.7 1 2.5 1 Z"/></svg>+330 5550-1928</li>
      <li><svg viewBox="0 0 12 12"><path d="M1 2.5 H11 V9.5 H1 Z M1.8 3.2 L6 6.4 L10.2 3.2 V8.8 H1.8 Z" fill-rule="evenodd"/></svg>info@pexla.com</li>
      <li><svg viewBox="0 0 12 12"><circle cx="6" cy="6" r="5"/><path d="M1 6 H11 M6 1 C3.5 3.5 3.5 8.5 6 11 M6 1 C8.5 3.5 8.5 8.5 6 11" stroke="#fff" stroke-width="0.8" fill="none"/></svg>www.pexla.com</li>
    </ul>
  </section>
</main>
</body>
</html>
```